Business card for marketing analytics company

Need a business card for new company. I have a logo already that I want to be built into the card and should use those colours

Company is called steered by tallies
Design must bring steered by tallies to life not be a card that could be for anyone with a logo put on it.

Like the front to be fairly clean and uncluttered bringing the logo out with a suitable design on the back of the card.

The logo represents a compass and business growth so those themes along with numbers, analytics , data are appropriate.
I'm often working with creative industries so also needs to reflect the creative side of analytics rather than be very corporate looking.

Target Market(s)

Ad agency, media agency, consumer goods clients

Industry/Entity Type

Market Research

Contact Information for Business Card

Needs to include name, title, email and phone number

Colors
f78f20
f68d4d
ec1f27

Requirements
Must have
• Must bring steered by tallies to life not be a card that could be for anyone with a logo put on it.
• Logo, Correct colours
• Like a design on the back that relates to company name
• Designs for both sides
Should not have
• Please do not just submit logo and a coloured card.
• It needs to have a design element to it
• No black background
• No clear cards - needs front & back

```html
<!DOCTYPE html>
<html lang="en">
<head>
<meta charset="utf-8">
<title>Steered by Tallies – Business Card</title>
<link href="https://fonts.googleapis.com/css2?family=Montserrat:wght@500&family=Open+Sans:wght@400;600&display=swap" rel="stylesheet">
<style>
  :root {
    --stage: #2b2b2b;
    --card-white: #ffffff;
    --brand-orange: #f47424;
    --brand-red: #c0202a;
    --brand-slate: #4f5960;
    --text-grey: #4a4a4a;
    --rule-grey: #8a8a8a;
    --faint-white: rgba(255, 255, 255, 0.14);
  }
  * { margin: 0; padding: 0; box-sizing: border-box; }
  html, body { width: 1200px; height: 987px; overflow: hidden; }
  body { background: var(--stage); position: relative; font-family: "Open Sans", sans-serif; }

  .card { position: absolute; left: 293px; width: 615px; height: 352px; overflow: hidden; }
  .card-front { top: 130px; background: var(--card-white); }
  .card-back { top: 505px; background: var(--brand-orange); }

  .wordmark-line { position: absolute; font-family: "Montserrat", sans-serif; font-weight: 500; line-height: 1; white-space: nowrap; }

  /* front */
  .brand-ring { position: absolute; left: 292px; top: 46px; width: 86px; height: 86px; border-radius: 50%; border: 3px solid var(--brand-orange); }
  .card-front .wordmark-line { color: var(--brand-slate); }
  .card-front .line-one { left: 401px; top: 34px; font-size: 28px; }
  .card-front .line-two { left: 443px; top: 66px; font-size: 29px; }

  .identity { position: absolute; left: 37px; top: 244px; display: flex; align-items: baseline; white-space: nowrap; }
  .person-name { color: var(--brand-orange); font-size: 20px; font-weight: 600; letter-spacing: 0.2px; }
  .identity-dash { color: var(--brand-orange); font-size: 20px; font-weight: 600; margin: 0 9px 0 14px; }
  .person-title { color: var(--brand-red); font-size: 17px; }
  .identity-rule { position: absolute; left: 37px; right: 37px; top: 276px; height: 1px; background: var(--rule-grey); }

  .contacts { position: absolute; left: 37px; top: 285px; display: flex; gap: 11px; font-size: 16px; color: var(--text-grey); white-space: nowrap; }
  .contact { display: flex; align-items: center; gap: 5px; }
  .contact svg { width: 15px; height: 15px; fill: var(--brand-orange); flex: none; }

  .accent-band { position: absolute; left: 0; bottom: 0; width: 615px; height: 12px; }

  /* back */
  .back-ring { position: absolute; left: 25px; top: 28px; width: 304px; height: 304px; border-radius: 50%; border: 14px solid var(--faint-white); }
  .card-back .wordmark-line { color: var(--card-white); }
  .card-back .line-one { left: 330px; top: 220px; font-size: 37px; }
  .card-back .line-two { left: 390px; top: 259px; font-size: 40px; }
  .back-url { position: absolute; left: 330px; top: 303px; color: var(--card-white); font-size: 14px; letter-spacing: 2px; white-space: nowrap; }
</style>
</head>
<body>

  <section class="card card-front" aria-label="Card front">
    <span class="brand-ring" aria-hidden="true"></span>
    <span class="wordmark-line line-one">Steered by</span>
    <span class="wordmark-line line-two">Tallies</span>

    <div class="identity">
      <span class="person-name">DANIEL MERCER</span>
      <span class="identity-dash">-</span>
      <span class="person-title">CEO/Founder</span>
    </div>
    <div class="identity-rule"></div>

    <div class="contacts">
      <span class="contact">
        <svg viewBox="0 0 24 24" aria-hidden="true"><path d="M6.6 10.8a15.1 15.1 0 0 0 6.6 6.6l2.2-2.2a1 1 0 0 1 1-.25 11.4 11.4 0 0 0 3.6.57 1 1 0 0 1 1 1V20a1 1 0 0 1-1 1A17 17 0 0 1 3 4a1 1 0 0 1 1-1h3.5a1 1 0 0 1 1 1c0 1.25.2 2.45.57 3.57a1 1 0 0 1-.25 1z"/></svg>
        555 214 7390
      </span>
      <span class="contact">
        <svg viewBox="0 0 24 24" aria-hidden="true"><path d="M2 5h20v14H2z"/><path d="M3 6l9 7 9-7" fill="none" stroke="#fff" stroke-width="1.6"/></svg>
        dan@steeredbytallies.com
      </span>
      <span class="contact">
        <svg viewBox="0 0 24 24" aria-hidden="true"><circle cx="12" cy="12" r="10"/><path d="M2 12h20M12 2c3 3 3 17 0 20M12 2c-3 3-3 17 0 20" fill="none" stroke="#fff" stroke-width="1.4"/></svg>
        steeredbytallies.com
      </span>
    </div>

    <svg class="accent-band" viewBox="0 0 615 12" preserveAspectRatio="none" aria-hidden="true">
      <polygon points="0,0 470,0 463,12 0,12" fill="var(--brand-orange)"/>
      <polygon points="473,0 546,0 539,12 466,12" fill="var(--brand-red)"/>
      <polygon points="549,0 615,0 615,12 542,12" fill="var(--brand-slate)"/>
    </svg>
  </section>

  <section class="card card-back" aria-label="Card back">
    <span class="back-ring" aria-hidden="true"></span>
    <span class="wordmark-line line-one">Steered by</span>
    <span class="wordmark-line line-two">Tallies</span>
    <span class="back-url">www.steeredbytallies.com</span>
  </section>

</body>
</html>
```